Business card for medical clinic

I need an upmarket, modern medical/health business card for my clinic

Contact Information for Business Card

name, address, email, qr code

```html
<!DOCTYPE html>
<html lang="en">
<head>
<meta charset="utf-8">
<title>Meridian Care Clinic – Business Card</title>
<link rel="stylesheet" href="https://fonts.googleapis.com/css2?family=Cinzel:wght@500&family=EB+Garamond:wght@400&display=swap">
<style>
  :root{
    --bg:#2a2a2a;
    --navy:#14365e;
    --blue-deep:#0d5a8f;
    --blue:#1b8fcf;
    --blue-light:#29a6e2;
    --paper:#f4f4f4;
    --ink:#555a60;
    --white:#ffffff;
  }
  *{box-sizing:border-box;margin:0;padding:0}
  html,body{width:1200px;height:852px;overflow:hidden;background:var(--bg)}
  .stage{position:relative;width:1200px;height:852px}
  .card{position:absolute;width:540px;height:308px;border-radius:22px;overflow:hidden;
        box-shadow:0 10px 24px rgba(0,0,0,.45)}
  .card--front{left:40px;top:272px;
        background:linear-gradient(110deg,var(--navy) 0%,var(--blue-deep) 45%,var(--blue) 100%)}
  .card--back{left:620px;top:272px;background:var(--paper)}

  .brand{display:flex;align-items:center;gap:12px;font-family:"Cinzel",serif;font-weight:500;white-space:nowrap}
  .brand__dot{width:18px;height:18px;border-radius:50%;flex:none}
  .card--front .brand{position:absolute;left:50%;top:50%;transform:translate(-50%,-50%);
        color:var(--white);font-size:30px;letter-spacing:1px}
  .card--front .brand__dot{background:var(--white)}
  .card--back .brand{position:absolute;left:32px;top:76px;color:var(--navy);font-size:19px;letter-spacing:.3px;gap:10px}
  .card--back .brand__dot{background:var(--navy);width:14px;height:14px}

  .contact{position:absolute;left:340px;top:66px;list-style:none;font-family:"EB Garamond",serif;
        font-size:13px;color:var(--ink);line-height:19px}
  .contact li{display:flex;align-items:center;gap:8px;white-space:nowrap}
  .contact svg{width:11px;height:11px;fill:var(--navy);flex:none}
  .contact .contact__address{padding-left:19px;margin-top:4px}

  .person{position:absolute;left:40px;bottom:58px;font-family:"EB Garamond",serif}
  .person__name{font-family:"Cinzel",serif;font-weight:500;font-size:20px;color:var(--navy);letter-spacing:.5px}
  .person__role{font-size:14px;color:var(--ink)}

  .band{position:absolute;left:0;top:0;width:540px;height:308px}
  .band__label{position:absolute;right:26px;bottom:40px;font-family:"Cinzel",serif;font-weight:500;
        font-size:13px;letter-spacing:1.5px;color:var(--white);white-space:nowrap}
</style>
</head>
<body>
<main class="stage">

  <section class="card card--front" aria-label="Card front">
    <div class="brand"><span class="brand__dot"></span>Meridian Care Clinic</div>
  </section>

  <section class="card card--back" aria-label="Card back">
    <svg class="band" viewBox="0 0 540 308" aria-hidden="true">
      <defs>
        <linearGradient id="bandGrad" x1="0" x2="1" y1="0" y2="0">
          <stop offset="0" stop-color="#14365e"/>
          <stop offset="0.5" stop-color="#0d5a8f"/>
          <stop offset="1" stop-color="#29a6e2"/>
        </linearGradient>
      </defs>
      <path d="M0 296 L300 282 Q316 281 322 270 L330 250 Q334 240 346 240 L540 240 L540 308 L0 308 Z" fill="url(#bandGrad)"/>
    </svg>

    <div class="brand"><span class="brand__dot"></span>Meridian Care Clinic</div>

    <ul class="contact">
      <li><svg viewBox="0 0 24 24"><path d="M6.6 10.8a15 15 0 0 0 6.6 6.6l2.2-2.2a1 1 0 0 1 1-.25 11.4 11.4 0 0 0 3.6.57 1 1 0 0 1 1 1V20a1 1 0 0 1-1 1A17 17 0 0 1 3 4a1 1 0 0 1 1-1h3.5a1 1 0 0 1 1 1c0 1.250.2 2.450.57 3.6a1 1 0 0 1-.25 1z"/></svg>0700-555-01234</li>
      <li><svg viewBox="0 0 24 24"><path d="M2 5h20v14H2zm2 2v.5l8 5 8-5V7zm0 3v7h16v-7l-8 5z"/></svg>hello@meridiancare.com</li>
      <li><svg viewBox="0 0 24 24"><path d="M12 2a10 10 0 1 0 0 20 10 10 0 0 0 0-20zm0 2c1 1.3 1.8 3 2.1 5H9.9C10.2 7 11 5.3 12 4zM4.3 11h3.6a15 15 0 0 0 0 2H4.3a8 8 0 0 1 0-2zm5.6 0h4.2a13 13 0 0 1 0 2H9.9a13 13 0 0 1 0-2zm6.2 0h3.6a8 8 0 0 1 0 2h-3.6a15 15 0 0 0 0-2zM9.9 15h4.2c-.3 2-1.100 3.7-2.100 5-1-1.3-1.800-3-2.100-5z"/></svg>www.meridiancare.com</li>
      <li class="contact__address">18 Elm Row, Town, US 10001</li>
    </ul>

    <div class="person">
      <p class="person__name">Daniel Harlow</p>
      <p class="person__role">Managing Director</p>
    </div>

    <p class="band__label">Meridian Care Clinic</p>
  </section>

</main>
</body>
</html>
```